Stationery Design Project

We need a stationery design for our Norwegian trucking company. We have existed for about 15 years and our 12 drivers uses relatively new vehicles to transport goods around in northern Norway. Long distance routes with fresh fish og food transport is our main operations.

We have already made alogo that's printed on our trucks. The logo and a picture of our trucks is attached. I think the logo i crappy, but since its already in use, changing it is not an option in this round. Still using a better colour scheme in the overall stationery and more interesting fonts is possible (altso in the logo).

Company details:
Name: Kjelvraket AS
Organisation nr 873 615 309
Post adress: 8642 Raudvik

I like minimalism and simplicity. I am avalibly for questions in normal GMT working hours either here or on mail: ivar@fjordlast.no

Reason: Hi. Im extending the deadline because I needed some time to find a vector file of our logo. Sorry for the inconvenience

Hi, and thanks for all your interest in the project. Some updates:

-          I have decided to commit to using one of the designs. Some designer will get the payment.

-          I have extended the deadline with 24 hours since I needed some time to find our firms vector logo (a slow Swedish man was holding me up)

-          We will not choose a design before the deadline. No need to rush.

-          We have received a lot of great design and think there is a need to specified the product we want to make:

o   Business Card for all our employers. I just need the design and will duplicate with the correct numbers and name myself. The information on should be: Logo, employer’s name, Phone number, email, website, Postal number and address. Use this as a template: logo, Leif Brattvoll, 47382066, Leif@fjordlast.no,, fjordlast.no, 8642 Raudvik. The order and placement of the information is your creative decision.

o   Stickers to put on the goods we travel. On the sticker the should be the following information: Logo, phone number, Tekst and link: Fraktæ av Kjelvraket. Ke du syns? Fjordlast.no/tilbakemelding (this means: Handled by Kjelvraket. What do you think Fjordlast.no/feedback -à the link will be a feedback form). The placement the information and size is your creative decision with some stings: we have been thinking of using Drukko for printing and see that a size about 6x6 cm, 8x5 or something like that. (with 3000 copies our budget is 200 punds). Any suggestions of other suppliers are welcome. Drukko price calculator http://www.drukkolabelhouse.co.uk/digital-litho-printing/printing-labels-tags/stickers/

o   Letterhead with logo, address, phone number and organizational number.

o   Envelopes with logo,address, phone number and organizational number.

Have a nice day.

 

 

• Using the blue colour in the logo and using a similar graphic approch.

```html
<!DOCTYPE html>
<html lang="no">
<head>
<meta charset="utf-8">
<title>Kjelvraket – stationery</title>
<link href="https://fonts.googleapis.com/css2?family=PT+Serif:ital,wght@0,400;0,700;1,400;1,700&display=swap" rel="stylesheet">
<style>
  :root{
    --bg:#cccccc;
    --paper:#ffffff;
    --navy:#0a0a8c;
    --blue:#2b55d3;
    --yellow:#ffcc00;
    --shadow:4px 5px 7px rgba(0,0,0,.45);
  }
  *{box-sizing:border-box;margin:0;padding:0}
  html,body{width:1200px;height:1000px;overflow:hidden;background:var(--bg)}
  body{position:relative;font-family:"PT Serif",Georgia,serif;color:var(--navy)}
  .piece{position:absolute;background:var(--paper);box-shadow:var(--shadow);overflow:hidden}
  .wave{position:absolute;left:0;bottom:0;width:100%;height:100%}
  .wordmark{position:absolute;display:flex;align-items:center;gap:6px;font-weight:700;color:var(--navy);white-space:nowrap}
  .wordmark .dot{display:block;border-radius:50%;background:var(--yellow)}
  .footer-line{position:absolute;right:22px;color:#fff;font-style:italic;font-size:7.5px;white-space:nowrap}

  /* letterhead */
  .letterhead{left:50px;top:256px;width:490px;height:691px}
  .letterhead .wordmark{right:26px;top:38px;font-size:24px}
  .letterhead .wordmark .dot{width:14px;height:14px}
  .letterhead .footer-line{bottom:10px}

  /* envelope */
  .envelope{left:590px;top:715px;width:558px;height:238px}
  .envelope .wordmark{right:36px;top:30px;font-size:24px}
  .envelope .wordmark .dot{width:14px;height:14px}
  .envelope .footer-line{bottom:7px}

  /* business cards */
  .card-back{position:absolute;width:330px;height:170px;box-shadow:var(--shadow)}
  .card-back.under{left:698px;top:292px;background:var(--navy);transform:rotate(13deg)}
  .card-back.top{left:702px;top:280px;background:var(--blue);transform:rotate(11deg);display:flex;align-items:center;justify-content:center}
  .card-back.top .wordmark{position:static;font-size:22px;color:var(--yellow)}
  .card-back.top .wordmark .dot{width:12px;height:12px;background:var(--navy)}
  .card-front{left:695px;top:467px;width:312px;height:178px}
  .card-front .wordmark{right:22px;top:42px;font-size:16px}
  .card-front .wordmark .dot{width:10px;height:10px}
  .holder{position:absolute;left:22px;top:38px}
  .holder .name{font-size:9px;letter-spacing:1.6px;text-transform:uppercase}
  .holder .role{font-size:7px;font-style:italic;letter-spacing:1.4px;margin:2px 0 0 24px}
  .contact{position:absolute;left:22px;top:70px;font-size:6.5px;font-style:italic;line-height:8.6px;letter-spacing:.6px}
  .contact li{list-style:none;display:flex;gap:16px}
  .contact .label{color:var(--yellow);font-weight:700;width:6px}
  .contact .addr{margin-left:22px}

  /* stickers */
  .sticker{position:absolute;display:flex;flex-direction:column;align-items:center;justify-content:center;text-align:center;border:6px solid #fff;box-shadow:var(--shadow)}
  .sticker .wordmark{position:static;font-size:15px}
  .sticker .wordmark .dot{width:9px;height:9px}
  .sticker .tag{font-weight:700;font-size:13px;margin-top:4px}
  .sticker .question{font-weight:700;font-size:25px;line-height:1}
  .sticker .link{font-weight:700;font-style:italic;font-size:11.5px;margin-top:2px}
  .sticker-oval{left:658px;top:40px;width:244px;height:155px;border-radius:50%;background:var(--blue);color:#fff}
  .sticker-oval::after{content:"";position:absolute;inset:5px;border:2px solid var(--yellow);border-radius:50%}
  .sticker-oval .wordmark{color:var(--yellow)}
  .sticker-oval .wordmark .dot{background:#fff}
  .sticker-round{left:940px;top:41px;width:152px;height:152px;border-radius:50%;background:var(--yellow);color:var(--navy)}
  .sticker-round .tag{font-size:9.5px}
  .sticker-round .question{font-size:18px}
  .sticker-round .link{font-size:8px}
  .sticker-round .wordmark{font-size:13px}
</style>
</head>
<body>

  <section class="sticker sticker-oval">
    <div class="wordmark"><span class="dot"></span>Kjelvraket</div>
    <p class="tag">Fraktæ av Kjelvraket.</p>
    <p class="question">Ke du syns?</p>
    <p class="link">Fjordlast.no/tilbakemelding</p>
  </section>

  <section class="sticker sticker-round">
    <div class="wordmark"><span class="dot"></span>Kjelvraket</div>
    <p class="tag">Fraktæ av Kjelvraket.</p>
    <p class="question">Ke du syns?</p>
    <p class="link">Fjordlast.no/tilbakemelding</p>
  </section>

  <section class="piece letterhead">
    <div class="wordmark"><span class="dot"></span>Kjelvraket</div>
    <svg class="wave" viewBox="0 0 490 691" preserveAspectRatio="none" aria-hidden="true">
      <path d="M150 667 Q420 652 490 574 L490 628 Q320 670 150 667Z" fill="var(--yellow)"/>
      <path d="M0 657 Q260 676 490 639 L490 691 L0 691Z" fill="var(--navy)"/>
    </svg>
    <p class="footer-line">8642 Raudvik, Sørvik, Nordland, Organisation: 873 615 309, Phone: 412 77 360</p>
  </section>

  <div class="card-back under"></div>
  <div class="card-back top">
    <div class="wordmark"><span class="dot"></span>Kjelvraket</div>
  </div>

  <section class="piece card-front">
    <div class="holder">
      <p class="name">Leif Brattvoll</p>
      <p class="role">Director, CEO</p>
    </div>
    <ul class="contact">
      <li><span class="label">p:</span><span>+47 47382066</span></li>
      <li><span class="label">e:</span><span>leif@fjordlast.no</span></li>
      <li><span class="label">w:</span><span>www.kjelvraket.no</span></li>
      <li class="addr">8642 Raudvik, Nordland</li>
    </ul>
    <div class="wordmark"><span class="dot"></span>Kjelvraket</div>
    <svg class="wave" viewBox="0 0 312 178" preserveAspectRatio="none" aria-hidden="true">
      <path d="M90 158 Q270 150 312 84 L312 122 Q220 160 90 158Z" fill="var(--yellow)"/>
      <path d="M0 151 Q170 166 312 130 L312 178 L0 178Z" fill="var(--navy)"/>
    </svg>
  </section>

  <section class="piece envelope">
    <div class="wordmark"><span class="dot"></span>Kjelvraket</div>
    <svg class="wave" viewBox="0 0 558 238" preserveAspectRatio="none" aria-hidden="true">
      <path d="M100 215 Q500 205 558 118 L558 160 Q380 215 100 215Z" fill="var(--yellow)"/>
      <path d="M0 205 Q300 222 558 180 L558 238 L0 238Z" fill="var(--navy)"/>
    </svg>
    <p class="footer-line">8642 Raudvik, Sørvik, Nordland, Organisation: 873 615 309, Phone: 412 77 360</p>
  </section>

</body>
</html>
```